Social Media Graphics - Oakline Push REVISED

Create 6-7 individual social media graphics (square size) to encourage folks to join our online course called:

The Harvest Ledger Circle
How to Launch a Multi-Million Business From Scratch
Sign Up Today!

IMPORTANT: Make the largest and most prominent text on the graphic be: How to Launch a Multi-Million Business From Scratch

For the color scheme of the graphics, let's try a blue color palette; make sure the graphics appeal to both men and women

Make sure each graphic contains 1 of the 3 pics attached (crop pic as needed); and make sure one of the graphics is all TEXT only.

Target Market(s)

men and women looking to start a business

Industry/Entity Type

Entrepreneurship

Colors
0054AA
0677BA
7BADD7
CADEEF
E8F1F8

Requirements
Must have
• All the text and use the 3 pics provided; one graphic can be all text; Simple, modern design that's easy to read

```html
<!DOCTYPE html>
<html lang="en">
<head>
<meta charset="utf-8">
<title>The Harvest Ledger Circle – Social Graphics</title>
<link rel="stylesheet" href="https://fonts.googleapis.com/css2?family=Anton&family=Poppins:wght@700;800;900&display=swap">
<style>
  :root{
    --blue-deep:#0054AA;
    --blue:#0677BA;
    --blue-soft:#7BADD7;
    --blue-pale:#CADEEF;
    --blue-mist:#E8F1F8;
    --sky:#3FA9E6;
    --cyan:#19C6E6;
    --ink:#1C2233;
    --white:#FFFFFF;
  }
  html,body{margin:0;padding:0;}
  body{
    width:1200px;height:817px;overflow:hidden;
    background:var(--white);position:relative;
  }
  .post{position:absolute;width:352px;height:352px;display:block;}
  .post svg{width:352px;height:352px;display:block;}
  .post--photo-top{left:40px;top:47px;}
  .post--text-only{left:427px;top:47px;}
  .post--duo-right{left:814px;top:47px;}
  .post--stage{left:40px;top:428px;}
  .post--bold-type{left:428px;top:426px;}
  .post--duo-bottom{left:816px;top:426px;}
  .condensed{font-family:'Anton',sans-serif;}
  .heavy{font-family:'Poppins',sans-serif;font-weight:800;}
  .black{font-family:'Poppins',sans-serif;font-weight:900;}
</style>
</head>
<body>

<!-- Post 1: hosts above headline -->
<div class="post post--photo-top">
<svg viewBox="0 0 680 680">
  <defs>
    <linearGradient id="p1-bg" x1="0" y1="0" x2="0" y2="1">
      <stop offset="0" stop-color="#3FA9E6"/><stop offset=".55" stop-color="#0677BA"/><stop offset="1" stop-color="#0054AA"/>
    </linearGradient>
    <linearGradient id="p1-photo" x1="0" y1="0" x2="0" y2="1">
      <stop offset="0" stop-color="#1E5C98" stop-opacity=".55"/><stop offset="1" stop-color="#0B2F5A" stop-opacity=".9"/>
    </linearGradient>
  </defs>
  <rect width="680" height="680" fill="url(#p1-bg)"/>
  <text class="heavy" x="340" y="60" font-size="42" fill="var(--white)" text-anchor="middle" textLength="610" lengthAdjust="spacingAndGlyphs">THE HARVEST LEDGER CIRCLE</text>
  <rect x="160" y="75" width="380" height="310" rx="20" fill="url(#p1-photo)" role="img" aria-label="Photo of the two course hosts smiling, arms crossed"/>
  <text class="condensed" x="340" y="472" font-size="100" fill="var(--white)" text-anchor="middle" textLength="555" lengthAdjust="spacingAndGlyphs">HOW TO LAUNCH</text>
  <text class="condensed" x="340" y="536" font-size="60" fill="var(--white)" text-anchor="middle" textLength="560" lengthAdjust="spacingAndGlyphs">A MULTI-MILLION BUSINESS</text>
  <rect x="0" y="552" width="680" height="69" fill="var(--ink)"/>
  <text class="heavy" x="340" y="611" font-size="66" fill="var(--white)" text-anchor="middle" textLength="570" lengthAdjust="spacingAndGlyphs">FROM SCRATCH</text>
  <rect x="0" y="621" width="680" height="59" fill="#0A5A9C"/>
  <text class="heavy" x="340" y="660" font-size="28" fill="var(--white)" text-anchor="middle" textLength="250" lengthAdjust="spacingAndGlyphs">SIGN UP TODAY!</text>
</svg>
</div>

<!-- Post 2: text only -->
<div class="post post--text-only">
<svg viewBox="0 0 680 680">
  <defs>
    <radialGradient id="p2-bg" cx=".5" cy=".45" r=".75">
      <stop offset="0" stop-color="#F6FAFD"/><stop offset=".6" stop-color="#E8F1F8"/><stop offset="1" stop-color="#CADEEF"/>
    </radialGradient>
    <linearGradient id="p2-btn" x1="0" y1="0" x2="1" y2="0">
      <stop offset="0" stop-color="#0677BA"/><stop offset="1" stop-color="#7BADD7"/>
    </linearGradient>
  </defs>
  <rect width="680" height="680" fill="url(#p2-bg)"/>
  <rect x="32" y="30" width="618" height="594" fill="none" stroke="var(--blue)" stroke-width="2" stroke-dasharray="6 5"/>
  <path d="M40 28 H650 Q640 95 600 95 H90 Q50 95 40 28 Z" fill="var(--blue)"/>
  <text class="condensed" x="342" y="82" font-size="50" fill="var(--white)" text-anchor="middle" textLength="515" lengthAdjust="spacingAndGlyphs">THE HARVEST LEDGER CIRCLE</text>
  <text class="condensed" x="340" y="190" font-size="80" fill="var(--ink)" text-anchor="middle" textLength="515" lengthAdjust="spacingAndGlyphs">HOW TO LAUNCH A</text>
  <line x1="80" y1="205" x2="600" y2="205" stroke="var(--blue-soft)" stroke-width="2"/>
  <text class="condensed" x="340" y="305" font-size="112" fill="var(--blue)" text-anchor="middle" textLength="520" lengthAdjust="spacingAndGlyphs">MULTI-MILLION</text>
  <text class="condensed" x="340" y="452" font-size="170" fill="var(--blue)" text-anchor="middle" textLength="520" lengthAdjust="spacingAndGlyphs">BUSINESS</text>
  <line x1="80" y1="470" x2="600" y2="470" stroke="var(--blue-soft)" stroke-width="2"/>
  <text class="black" x="340" y="540" font-size="72" fill="var(--ink)" text-anchor="middle" textLength="518" lengthAdjust="spacingAndGlyphs">FROM SCRATCH</text>
  <rect x="160" y="595" width="362" height="57" rx="28" fill="url(#p2-btn)"/>
  <text class="heavy" x="341" y="635" font-size="34" fill="var(--white)" text-anchor="middle" textLength="295" lengthAdjust="spacingAndGlyphs">SIGN UP TODAY!</text>
</svg>
</div>

<!-- Post 3: hosts bottom right -->
<div class="post post--duo-right">
<svg viewBox="0 0 680 680">
  <defs>
    <linearGradient id="p3-bg" x1="0" y1="0" x2="1" y2="1">
      <stop offset="0" stop-color="#0054AA"/><stop offset=".5" stop-color="#0677BA"/><stop offset="1" stop-color="#19C6E6"/>
    </linearGradient>
    <linearGradient id="p3-panel" x1="0" y1="0" x2="1" y2="0">
      <stop offset="0" stop-color="#1C2233"/><stop offset=".6" stop-color="#1C2233"/><stop offset="1" stop-color="#1F3D8A"/>
    </linearGradient>
    <linearGradient id="p3-photo" x1="0" y1="0" x2="1" y2="0">
      <stop offset="0" stop-color="#1C2233" stop-opacity=".85"/><stop offset=".5" stop-color="#2A2A33" stop-opacity=".85"/><stop offset="1" stop-color="#D8405A" stop-opacity=".8"/>
    </linearGradient>
  </defs>
  <rect width="680" height="680" fill="url(#p3-bg)"/>
  <rect width="680" height="66" fill="var(--ink)"/>
  <text class="heavy" x="340" y="46" font-size="34" fill="var(--white)" text-anchor="middle" textLength="570" lengthAdjust="spacingAndGlyphs">THE <tspan fill="var(--cyan)">HARVEST LEDGER</tspan> CIRCLE</text>
  <line x1="62" y1="103" x2="120" y2="103" stroke="var(--white)" stroke-width="3"/>
  <line x1="556" y1="103" x2="625" y2="103" stroke="var(--white)" stroke-width="3"/>
  <text class="heavy" x="340" y="118" font-size="44" fill="var(--white)" text-anchor="middle" textLength="400" lengthAdjust="spacingAndGlyphs">HOW TO LAUNCH</text>
  <text class="condensed" x="340" y="210" font-size="92" fill="var(--white)" text-anchor="middle" textLength="578" lengthAdjust="spacingAndGlyphs">A MULTI-MILLION</text>
  <text class="condensed" x="340" y="372" font-size="180" fill="var(--white)" text-anchor="middle" textLength="578" lengthAdjust="spacingAndGlyphs">BUSINESS</text>
  <rect x="0" y="392" width="400" height="194" fill="url(#p3-panel)"/>
  <text class="black" x="48" y="470" font-size="80" fill="var(--white)" textLength="255" lengthAdjust="spacingAndGlyphs">FROM</text>
  <text class="condensed" x="48" y="555" font-size="90" fill="var(--white)" textLength="255" lengthAdjust="spacingAndGlyphs">SCRATCH</text>
  <text class="condensed" x="42" y="636" font-size="32" fill="var(--white)" textLength="240" lengthAdjust="spacingAndGlyphs">SIGN UP TODAY!</text>
  <rect x="330" y="395" width="350" height="285" rx="18" fill="url(#p3-photo)" role="img" aria-label="Photo of the two course hosts smiling, arms crossed"/>
</svg>
</div>

<!-- Post 4: stage photo with type column -->
<div class="post post--stage">
<svg viewBox="0 0 680 680">
  <defs>
    <linearGradient id="p4-bar" x1="0" y1="0" x2="1" y2="0">
      <stop offset="0" stop-color="#2A4FC8"/><stop offset="1" stop-color="#3A6AE0"/>
    </linearGradient>
    <linearGradient id="p4-photo" x1="0" y1="0" x2="0" y2="1">
      <stop offset="0" stop-color="#1F4FC0"/><stop offset=".55" stop-color="#0B2F7A"/><stop offset="1" stop-color="#1C2233"/>
    </linearGradient>
  </defs>
  <rect width="680" height="680" fill="var(--white)"/>
  <rect x="0" y="0" width="368" height="25" fill="url(#p4-bar)"/>
  <line x1="18" y1="62" x2="62" y2="62" stroke="var(--ink)" stroke-width="3"/>
  <line x1="618" y1="62" x2="662" y2="62" stroke="var(--ink)" stroke-width="3"/>
  <text class="condensed" x="340" y="80" font-size="46" fill="var(--ink)" text-anchor="middle" textLength="520" lengthAdjust="spacingAndGlyphs"><tspan fill="var(--blue)">THE </tspan>HARVEST LEDGER<tspan fill="var(--blue)"> CIRCLE</tspan></text>
  <rect x="0" y="98" width="368" height="582" fill="url(#p4-photo)" role="img" aria-label="Photo of the two hosts speaking on stage with a microphone"/>
  <text class="condensed" x="516" y="195" font-size="100" fill="var(--ink)" text-anchor="middle" textLength="248" lengthAdjust="spacingAndGlyphs">HOW TO</text>
  <text class="condensed" x="516" y="268" font-size="76" fill="var(--ink)" text-anchor="middle" textLength="248" lengthAdjust="spacingAndGlyphs">LAUNCH A</text>
  <line x1="400" y1="285" x2="635" y2="285" stroke="var(--blue-soft)" stroke-width="2"/>
  <text class="black" x="516" y="365" font-size="80" fill="var(--blue)" text-anchor="middle" textLength="245" lengthAdjust="spacingAndGlyphs">MULTI</text>
  <text class="black" x="516" y="425" font-size="58" fill="var(--blue)" text-anchor="middle" textLength="245" lengthAdjust="spacingAndGlyphs">MILLION</text>
  <text class="condensed" x="516" y="500" font-size="78" fill="var(--blue)" text-anchor="middle" textLength="248" lengthAdjust="spacingAndGlyphs">BUSINESS</text>
  <line x1="400" y1="512" x2="635" y2="512" stroke="var(--blue-soft)" stroke-width="2"/>
  <text class="condensed" x="516" y="568" font-size="52" fill="var(--ink)" text-anchor="middle" textLength="248" lengthAdjust="spacingAndGlyphs">FROM SCRATCH</text>
  <rect x="368" y="586" width="312" height="69" fill="var(--ink)"/>
  <text class="heavy" x="516" y="630" font-size="24" fill="var(--white)" text-anchor="middle" textLength="235" lengthAdjust="spacingAndGlyphs">SIGN UP TODAY!</text>
</svg>
</div>

<!-- Post 5: bold type -->
<div class="post post--bold-type">
<svg viewBox="0 0 680 680">
  <defs>
    <radialGradient id="p5-bg" cx=".5" cy=".4" r=".7">
      <stop offset="0" stop-color="#F6FAFD"/><stop offset="1" stop-color="#CADEEF"/>
    </radialGradient>
    <linearGradient id="p5-multi" x1="0" y1="0" x2="1" y2="0">
      <stop offset="0" stop-color="#7BADD7"/><stop offset="1" stop-color="#0054AA"/>
    </linearGradient>
    <linearGradient id="p5-band" x1="0" y1="0" x2="1" y2="1">
      <stop offset="0" stop-color="#0054AA"/><stop offset="1" stop-color="#0677BA"/>
    </linearGradient>
  </defs>
  <rect width="680" height="680" fill="url(#p5-bg)"/>
  <rect x="0" y="27" width="680" height="60" fill="var(--blue)"/>
  <text class="heavy" x="340" y="72" font-size="40" fill="var(--white)" text-anchor="middle" textLength="525" lengthAdjust="spacingAndGlyphs">THE HARVEST LEDGER CIRCLE</text>
  <text class="heavy" x="340" y="160" font-size="52" fill="var(--ink)" text-anchor="middle" textLength="520" lengthAdjust="spacingAndGlyphs">HOW TO LAUNCH A</text>
  <text class="black" x="340" y="340" font-size="200" fill="url(#p5-multi)" text-anchor="middle" textLength="520" lengthAdjust="spacingAndGlyphs">MULTI</text>
  <text class="black" x="340" y="476" font-size="175" fill="#0A4D8C" text-anchor="middle" textLength="525" lengthAdjust="spacingAndGlyphs">MILLION</text>
  <rect x="0" y="476" width="680" height="204" fill="url(#p5-band)"/>
  <text class="condensed" x="340" y="567" font-size="66" fill="var(--white)" text-anchor="middle" textLength="548" lengthAdjust="spacingAndGlyphs">BUSINESS FROM SCRATCH</text>
  <rect x="185" y="598" width="310" height="48" rx="24" fill="var(--ink)"/>
  <text class="heavy" x="340" y="633" font-size="30" fill="var(--white)" text-anchor="middle" textLength="255" lengthAdjust="spacingAndGlyphs">SIGN UP TODAY!</text>
</svg>
</div>

<!-- Post 6: hosts under headline -->
<div class="post post--duo-bottom">
<svg viewBox="0 0 680 680">
  <defs>
    <linearGradient id="p6-bg" x1="0" y1="0" x2="1" y2="1">
      <stop offset="0" stop-color="#0054AA"/><stop offset=".6" stop-color="#0677BA"/><stop offset="1" stop-color="#19C6E6"/>
    </linearGradient>
    <linearGradient id="p6-photo" x1="0" y1="0" x2="0" y2="1">
      <stop offset="0" stop-color="#1E5C98" stop-opacity=".5"/><stop offset="1" stop-color="#0B2F5A" stop-opacity=".9"/>
    </linearGradient>
  </defs>
  <rect width="680" height="680" fill="url(#p6-bg)"/>
  <path d="M0 0 H680 V0 Q672 70 630 70 H50 Q8 70 0 0 Z" fill="var(--white)"/>
  <text class="condensed" x="340" y="55" font-size="50" fill="var(--ink)" text-anchor="middle" textLength="555" lengthAdjust="spacingAndGlyphs">THE <tspan fill="var(--cyan)">HARVEST LEDGER</tspan> CIRCLE</text>
  <text class="condensed" x="340" y="180" font-size="100" fill="var(--white)" text-anchor="middle" textLength="555" lengthAdjust="spacingAndGlyphs">HOW TO LAUNCH</text>
  <text class="condensed" x="340" y="245" font-size="60" fill="var(--white)" text-anchor="middle" textLength="560" lengthAdjust="spacingAndGlyphs">A MULTI-MILLION BUSINESS</text>
  <text class="condensed" x="340" y="347" font-size="100" fill="var(--white)" text-anchor="middle" textLength="565" lengthAdjust="spacingAndGlyphs">FROM SCRATCH</text>
  <rect x="125" y="360" width="440" height="255" rx="18" fill="url(#p6-photo)" role="img" aria-label="Photo of the two course hosts smiling, arms crossed"/>
  <rect x="0" y="615" width="680" height="65" fill="var(--ink)"/>
  <text class="heavy" x="340" y="659" font-size="30" fill="var(--white)" text-anchor="middle" textLength="250" lengthAdjust="spacingAndGlyphs">SIGN UP TODAY!</text>
</svg>
</div>

</body>
</html>
```